gift box for organic and natural food items

My brand name is Tiller's Pantry and we are selling organic dried food to Korea now. We focus on transparent from the family farm to the customer directly with the single or simple organic ingredient. Our main customers are mainly woman from 30 to 50 years old. We have 4 different products for this package. Organic dried cherry, Organic dried figs, Organic dried dates and Organic dried pistachio. I would like to make a gift box that woman want to have and hold our natural products. The material of the gift box will be Royal Ivory Paper.

Target Market(s)

We will sell these items and gift box at the luxury department store.

Industry/Entity Type

Food Production

Font styles to use
Serif
Script

Colors
9ccb3b

Requirements
Must have
• Our slogan: A gift from the farm brought fresh to your door
• Our producer image: I will upload our producer's image
• We focus on the transparent and our producers.
• I will provide you with the image file for the only producers later.
Nice to have
• Brand logo / Our brand introduction sentences / NFCB logo / Color
• Color : Green & Bright Beige
• "Indulge. Nourish. Enjoy"
• "Taste the difference.
• The difference is quality.
• Quality you can experience"
• "As you savor the farm fresh delicacies enclosed in every box, relish in the fact that each ingredient was meticulously selected and directly sourced from hard working family farms. The result is a snacking experience like none other. With quality you can taste, our organic treats boast a unique flavor that will tantalize the taste buds. "
• "Upgrade your nourishment.
• Upgrade your nutrition.
• Upgrade your snack."
Should not have
• Too complicated with many colors

```html
<!DOCTYPE html>
<html lang="en">
<head>
<meta charset="utf-8">
<title>Tiller's Pantry – Gift Box Dieline</title>
<link rel="stylesheet" href="https://fonts.googleapis.com/css2?family=Playfair+Display:wght@700&family=Raleway:wght@400;500&family=Noto+Sans+KR:wght@400&display=swap">
<style>
  :root {
    --paper: #ffffff;
    --box-green: #5db774;
    --panel-beige: #e8d9bf;
    --flap-beige: #e4cba8;
    --brand-green: #2f9a5c;
    --cut-line: #e0443a;
    --fold-line: #4a5aa8;
    --spec-frame: #a64c9a;
  }
  html, body {
    margin: 0;
    padding: 0;
    width: 1200px;
    height: 770px;
    overflow: hidden;
    background: var(--paper);
  }
  .dieline {
    display: block;
    width: 1200px;
    height: 770px;
  }
  .green-face { fill: var(--box-green); }
  .beige-face { fill: var(--panel-beige); }
  .bottom-flap { fill: var(--flap-beige); stroke: var(--cut-line); stroke-width: 1; }
  .cut { fill: none; stroke: var(--cut-line); stroke-width: 1; }
  .fold { fill: none; stroke: var(--fold-line); stroke-width: 1; }
  .handle-hole { fill: #ffffff; stroke: var(--cut-line); stroke-width: 1; }
  .spec-frame { fill: #ffffff; stroke: var(--spec-frame); stroke-width: 1; }
  .spec-text {
    font-family: "Noto Sans KR", sans-serif;
    font-size: 10px;
    fill: #333333;
  }
  .brand-name {
    font-family: "Playfair Display", serif;
    font-weight: 700;
    font-size: 26px;
    fill: var(--brand-green);
  }
  .brand-dot { fill: var(--box-green); opacity: 0.55; }
  .slogan-bar { fill: var(--box-green); }
  .slogan-text {
    font-family: "Raleway", sans-serif;
    font-size: 7.6px;
    fill: #ffffff;
  }
  .tagline {
    font-family: "Raleway", sans-serif;
    font-size: 11.5px;
    letter-spacing: 0.9px;
    fill: var(--box-green);
  }
  .cert-badge { fill: #ffffff; stroke: var(--brand-green); stroke-width: 3; }
  .cert-badge-inner { fill: var(--brand-green); }
</style>
</head>
<body>
<svg class="dieline" viewBox="0 0 1500 963" xmlns="http://www.w3.org/2000/svg">
  <defs>
    <radialGradient id="splash-left" cx="85%" cy="35%" r="80%">
      <stop offset="0" stop-color="#d4e02e"/>
      <stop offset="0.35" stop-color="#9ccb3b"/>
      <stop offset="1" stop-color="#5db774"/>
    </radialGradient>
    <radialGradient id="splash-right" cx="10%" cy="40%" r="80%">
      <stop offset="0" stop-color="#d4e02e"/>
      <stop offset="0.35" stop-color="#9ccb3b"/>
      <stop offset="1" stop-color="#5db774"/>
    </radialGradient>
    <linearGradient id="portrait-sketch" x1="0" y1="0" x2="0" y2="1">
      <stop offset="0" stop-color="#c9c3b6"/>
      <stop offset="1" stop-color="#8d8a84"/>
    </linearGradient>
    <linearGradient id="portrait-photo" x1="0" y1="0" x2="0" y2="1">
      <stop offset="0" stop-color="#c7b9a3"/>
      <stop offset="1" stop-color="#56709f"/>
    </linearGradient>
  </defs>

  <!-- Job specification box -->
  <g class="job-spec">
    <rect class="spec-frame" x="245" y="64" width="204" height="132"/>
    <rect class="spec-frame" x="249" y="68" width="196" height="124"/>
    <text class="spec-text" x="263" y="101">업체: 틸러스팬트리</text>
    <text class="spec-text" x="263" y="117">품명: 체리5입,피스타치오2입 공용</text>
    <text class="spec-text" x="263" y="133">재질: 무광 RIV 350</text>
    <text class="spec-text" x="263" y="149">특이사항:</text>
    <text class="spec-text" x="263" y="165">작업일: 19.07.26</text>
  </g>

  <!-- Glue flap -->
  <path class="green-face" d="M108 258 L142 249 L142 710 L120 704 Q108 700 108 686 Z"/>
  <path class="cut" d="M142 249 L108 258 L108 686 Q108 700 120 704 L142 710"/>

  <!-- Front panel -->
  <g class="front-panel">
    <rect class="beige-face" x="142" y="249" width="411" height="454"/>
    <rect class="green-face" x="142" y="703" width="411" height="7"/>
    <path role="img" aria-label="Green and lime brush-stroke splash decoration" fill="url(#splash-left)"
          d="M553 270 Q480 290 455 390 Q430 500 455 600 Q485 680 553 695 Z"/>
    <rect class="handle-hole" x="270" y="282" width="154" height="48" rx="24"/>
    <rect class="handle-hole" x="313" y="349" width="68" height="5" rx="2.5"/>
    <circle class="brand-dot" cx="216" cy="400" r="11"/>
    <text class="brand-name" x="232" y="412" textLength="151" lengthAdjust="spacingAndGlyphs">Tiller's Pantry</text>
    <rect class="slogan-bar" x="205" y="451" width="178" height="13"/>
    <text class="slogan-text" x="209" y="460.5" textLength="170" lengthAdjust="spacingAndGlyphs">A gift from the farm brought fresh to your door</text>
    <text class="tagline" x="205" y="483">"Taste the difference.</text>
    <text class="tagline" x="205" y="501">The difference is quality.</text>
    <text class="tagline" x="205" y="519">Quality you can experience"</text>
    <rect role="img" aria-label="Pencil-sketch portraits of the four family-farm producers" fill="url(#portrait-sketch)"
          x="147" y="578" width="378" height="125" rx="30"/>
    <circle class="cert-badge" cx="510" cy="688" r="18"/>
    <circle class="cert-badge-inner" cx="510" cy="688" r="10"/>
  </g>

  <!-- Left side panels -->
  <path class="green-face" d="M553 249 L660 258 L766 249 L766 710 L553 710 Z"/>
  <path class="cut" d="M553 249 L660 258 L766 249"/>
  <path class="fold" d="M660 258 L660 604 M553 710 L660 604 L766 710"/>
  <path class="green-face" d="M555 712 L605 817 L660 817 L766 712 Z"/>
  <path class="cut" d="M555 712 L605 817 L660 817 L766 712"/>

  <!-- Back panel with carry handle flap -->
  <g class="back-panel">
    <path class="green-face" d="M766 249 L766 118 Q766 103 781 103 L1163 103 Q1178 103 1178 118 L1178 249 Z"/>
    <path class="cut" d="M766 249 L766 118 Q766 103 781 103 L1163 103 Q1178 103 1178 118 L1178 249"/>
    <path class="fold" d="M766 240 L1178 240"/>
    <path class="cut" d="M936 135 Q950 128 962 140 Q972 150 984 140 Q996 128 1010 135"/>
    <rect class="handle-hole" x="900" y="160" width="146" height="40" rx="20"/>
    <rect class="beige-face" x="766" y="249" width="412" height="454"/>
    <rect class="green-face" x="766" y="703" width="412" height="7"/>
    <path role="img" aria-label="Green and lime brush-stroke splash decoration" fill="url(#splash-right)"
          d="M768 270 Q855 300 882 400 Q905 500 875 600 Q845 675 768 690 Z"/>
    <rect class="handle-hole" x="900" y="285" width="146" height="42" rx="21"/>
    <circle class="brand-dot" cx="955" cy="400" r="11"/>
    <text class="brand-name" x="971" y="412" textLength="151" lengthAdjust="spacingAndGlyphs">Tiller's Pantry</text>
    <rect class="slogan-bar" x="944" y="451" width="178" height="13"/>
    <text class="slogan-text" x="948" y="460.5" textLength="170" lengthAdjust="spacingAndGlyphs">A gift from the farm brought fresh to your door</text>
    <text class="tagline" x="944" y="483">"Taste the difference.</text>
    <text class="tagline" x="944" y="501">The difference is quality.</text>
    <text class="tagline" x="944" y="519">Quality you can experience"</text>
    <rect role="img" aria-label="Colour photographs of the four family-farm producers" fill="url(#portrait-photo)"
          x="878" y="612" width="294" height="91" rx="24"/>
    <circle class="cert-badge" cx="815" cy="688" r="18"/>
    <circle class="cert-badge-inner" cx="815" cy="688" r="10"/>
  </g>

  <!-- Right side panels -->
  <path class="green-face" d="M1178 249 L1285 258 L1392 249 L1392 710 L1178 710 Z"/>
  <path class="cut" d="M1178 249 L1285 258 L1392 249 L1392 710"/>
  <path class="fold" d="M1285 258 L1285 604 M1178 710 L1285 604 L1392 710"/>
  <path class="green-face" d="M1180 712 L1230 817 L1285 817 L1390 712 Z"/>
  <path class="cut" d="M1180 712 L1230 817 L1285 817 L1390 712"/>

  <!-- Bottom lock flaps -->
  <path class="bottom-flap" d="M142 710 L553 710 L548 720 L548 848 Q548 858 538 858 L495 858 L446 818 L347 818 L312 858 L160 858 Q150 858 150 848 L150 720 Z"/>
  <path class="fold" d="M446 818 L548 720"/>
  <path class="bottom-flap" d="M768 710 L1178 710 L1170 720 L1170 848 Q1170 858 1160 858 L1118 858 L1072 818 L974 818 L940 858 L787 858 Q777 858 777 848 L777 720 Z"/>
  <path class="fold" d="M1072 818 L1170 720"/>
</svg>
</body>
</html>
```